tinyTally Resource Book - 10 maths tasks to do outside

I need a 22 (11 pages back to back) page A6 sized book produced to standard for submission to professional printer. Needs to be as .pdf file showing guide lines and allowances for colour bleed. I have text already written and submitted as attachment in a Word file with margins set to A6 size. The theme of the materials is "Nature Play" so using lots of pictures from nature (Australia preferably) and showing lots of patterns in nature (rocks, leaves, flower petals etc). Some of the tasks refer to specific activities, such as "shadows" and "floating" so would be great to illustrate appropriately. The big emphasis is on learning outside the classroom, getting kids to engage actively with nature. I would like to see the pages as full colour - so not white background. The book itself will be spiral bound along the top edge so a margin of at least 1cm will be required at the top of each page (or the bottom of even numbered pages). Book will be printed on plastic laminated matte paper for outdoor use. Font size needs to be big enough to read. Fonts sizes, alignments and page numbers are all different at the moment and need to be standardised. One photo is included in a page as a sample if you can use it, otherwise disregard. Logo for Wattlebrook Numeracy Guild is also included to have as part of the acknowledgements at the back of the book.

Target Market(s)

Book is for early childhood and preschool teachers.

Industry/Entity Type

Education

Font styles to use
Sans Serif

Requirements
Must have
• Colour and appeal.
Nice to have
• Use of natural colours instead of bright catchy colours but that is your call.
Should not have
• American spelling

```html
<!DOCTYPE html>
<html lang="en-AU">
<head>
<meta charset="utf-8">
<title>One More – Task Card</title>
<link rel="stylesheet" href="https://fonts.googleapis.com/css2?family=Jost:ital,wght@0,400;0,600;0,700;1,600;1,700&display=swap">
<style>
  :root {
    --paper: #ffffff;
    --wood-light: #f2c592;
    --wood-mid: #e8b27a;
    --wood-dark: #dea46a;
    --heading-blue: #2f3b8f;
    --accent-blue: #3840a0;
    --body-ink: #3a302c;
    --bullet-red: #d0202a;
    --crop-line: #555555;
    --leaf-green: #b7d64a;
    --leaf-deep: #7fae2c;
  }
  * { margin: 0; padding: 0; box-sizing: border-box; }
  html, body { width: 892px; height: 1200px; overflow: hidden; background: var(--paper); }
  .page {
    position: relative;
    width: 892px;
    height: 1200px;
    font-family: "Jost", "Futura", sans-serif;
  }
  .crop-marks { position: absolute; inset: 0; }
  .card-surface {
    position: absolute;
    left: 54px; top: 56px;
    width: 784px; height: 1090px;
    background: linear-gradient(90deg, var(--wood-mid) 0%, var(--wood-light) 25%, var(--wood-mid) 50%, var(--wood-light) 75%, var(--wood-dark) 100%);
  }
  .task-title {
    position: absolute;
    top: 102px; left: 0; width: 892px;
    text-align: center;
    font-size: 47px;
    font-weight: 700;
    color: var(--heading-blue);
    text-shadow: -2px -2px 0 #fff, 2px -2px 0 #fff, -2px 2px 0 #fff, 2px 2px 0 #fff, 3px 4px 4px rgba(0,0,0,.35);
  }
  .outcome {
    position: absolute;
    top: 172px; left: 120px; width: 652px;
    text-align: center;
    font-size: 30px;
    line-height: 42px;
    font-weight: 700;
    color: var(--heading-blue);
    text-shadow: -1px -1px 0 #fff, 1px -1px 0 #fff, -1px 1px 0 #fff, 1px 1px 0 #fff, 2px 3px 3px rgba(0,0,0,.3);
  }
  .section-lead {
    position: absolute;
    left: 126px;
    font-size: 24px;
    font-weight: 700;
    font-style: italic;
    color: var(--accent-blue);
  }
  .section-body {
    position: absolute;
    left: 196px;
    font-size: 32px;
    line-height: 45px;
    color: var(--body-ink);
  }
  .opportunities {
    position: absolute;
    left: 196px; top: 650px;
    list-style: none;
    font-size: 30px;
    line-height: 42px;
    color: var(--body-ink);
  }
  .opportunities li {
    position: relative;
    padding-left: 22px;
  }
  .opportunities li::before {
    content: "";
    position: absolute;
    left: 1px; top: 12px;
    width: 15px; height: 15px;
    background: var(--bullet-red);
    transform: rotate(45deg);
  }
  .leaf-sprigs {
    position: absolute;
    left: 532px; top: 808px;
    width: 224px; height: 232px;
    border-radius: 50%;
    background: radial-gradient(ellipse at center, var(--leaf-green) 0%, var(--leaf-deep) 45%, rgba(127,174,44,0) 72%);
    opacity: .75;
  }
</style>
</head>
<body>
<div class="page">
  <div class="card-surface" role="img" aria-label="Light bamboo wood-grain background"></div>

  <svg class="crop-marks" width="892" height="1200" viewBox="0 0 892 1200" aria-hidden="true">
    <g stroke="var(--crop-line)" stroke-width="1" fill="none">
      <line x1="54" y1="0" x2="54" y2="40"/><line x1="74" y1="36" x2="74" y2="74"/>
      <line x1="0" y1="56" x2="40" y2="56"/><line x1="36" y1="74" x2="74" y2="74"/>
      <line x1="838" y1="0" x2="838" y2="40"/><line x1="818" y1="36" x2="818" y2="74"/>
      <line x1="852" y1="56" x2="892" y2="56"/><line x1="818" y1="74" x2="856" y2="74"/>
      <line x1="54" y1="1160" x2="54" y2="1200"/><line x1="74" y1="1126" x2="74" y2="1164"/>
      <line x1="0" y1="1146" x2="40" y2="1146"/><line x1="36" y1="1126" x2="74" y2="1126"/>
      <line x1="838" y1="1160" x2="838" y2="1200"/><line x1="818" y1="1126" x2="818" y2="1164"/>
      <line x1="852" y1="1146" x2="892" y2="1146"/><line x1="818" y1="1126" x2="856" y2="1126"/>
    </g>
  </svg>

  <h1 class="task-title">4. One More</h1>
  <h2 class="outcome">EYLF – Outcome 2: Children are connected with and contribute to their world</h2>

  <p class="section-lead" style="top:313px">Children become aware of fairness when they...</p>
  <p class="section-body" style="top:352px">are empowered to make choices<br>and problem solve to meet their<br>needs in particular contexts</p>

  <p class="section-lead" style="top:485px">Educators promote this learning when they...</p>
  <p class="section-body" style="top:524px">engage children in discussions about<br>respectful and equal relations</p>

  <p class="section-lead" style="top:612px">This task provides an opportunity to:</p>
  <ul class="opportunities">
    <li>explore the concepts of “equal” and<br>“more”</li>
    <li>discuss how inequity<br>happens</li>
    <li>explore sharing equally</li>
    <li>develop strategies for<br>dealing with inequity</li>
  </ul>

  <div class="leaf-sprigs" role="img" aria-label="Two sprigs of fresh green leaves"></div>
</div>
</body>
</html>
```